Enhance Landing Page

Actual: https://thecoralparlor.com/aplique-no-litoral-lp-port/

I need a better design for this page:
Using this shortcodes : https://bolder.qrxlayouts.net
Rules:
. Keep the page header
. Keep the footer

```html
<!DOCTYPE html>
<html lang="en">
<head>
<meta charset="utf-8">
<title>The Coral Parlor – Invest in Florida</title>
<link href="https://fonts.googleapis.com/css2?family=Lato:wght@400;700;900&display=swap" rel="stylesheet">
<style>
:root{
  --purple:#3b1a63;
  --orange:#f5821f;
  --green:#2db742;
  --pink:#d81b60;
  --teal:#1596ad;
  --red:#d4163d;
  --grey-bg:#ececec;
  --line:#cfcfcf;
  --text:#333;
  --white:#fff;
  --black:#111;
}
*{box-sizing:border-box;margin:0;padding:0}
html,body{width:1200px;height:4018px;overflow:hidden}
body{position:relative;font-family:'Lato',sans-serif;color:var(--text);background:var(--white)}
.abs{position:absolute}
.btn{position:absolute;display:flex;align-items:center;justify-content:center;font-weight:700;color:var(--white);font-size:19px;border-radius:3px}
.btn-orange{background:var(--orange)}
.pill{position:absolute;background:var(--green);color:#fff;font-weight:900;font-size:15px;border-radius:4px;display:flex;align-items:center;gap:8px;padding:0 12px}
.pill .dot{width:16px;height:16px;border-radius:50%;background:#fff}
.phones{position:absolute;display:flex;gap:22px;font-size:13px;font-weight:700;color:var(--text);align-items:center}
.flag{display:inline-block;width:18px;height:12px;margin-right:5px;vertical-align:-1px;border-radius:2px}
.flag-br{background:#1f9e45}
.flag-us{background:linear-gradient(#b22234 0 33%,#fff 33% 66%,#3c3b6e 66%)}
.contact-link{position:absolute;display:flex;align-items:center;gap:10px;font-size:14px;font-weight:900;color:var(--purple);line-height:1.05;text-transform:uppercase}
.contact-link .ico{width:36px;height:36px;border-radius:50%;display:flex;align-items:center;justify-content:center}
.brand{position:absolute;text-align:center;font-weight:900;color:var(--purple);letter-spacing:2px}
/* header */
.site-header{position:absolute;top:0;left:0;width:1200px;height:86px;background:#fff;z-index:2}
.logo-tab{position:absolute;left:505px;top:0;width:190px;height:122px;background:#fff;border-radius:0 0 95px 95px/0 0 40px 40px;z-index:3}
.logo-tab .brand{left:0;width:190px;top:22px;font-size:30px;line-height:1}
.logo-tab .brand small{display:block;font-size:14px;letter-spacing:6px;margin-top:4px}
/* hero */
.hero{position:absolute;top:86px;left:0;width:1200px;height:576px;background:linear-gradient(180deg,#3a3a4a 0%,#8a5a3a 38%,#c07a3e 52%,#3e4a2a 70%,#1f3a14 100%)}
.hero h1{position:absolute;top:228px;width:1200px;text-align:center;color:#fff;font-weight:900;font-size:45px;line-height:45px;text-transform:uppercase}
.hero .arrow{position:absolute;top:262px;width:24px;height:40px}
/* gifts */
.gifts h2{position:absolute;left:75px;top:708px;font-size:28px;font-weight:700;color:var(--purple)}
.gifts p{position:absolute;left:75px;width:510px;font-size:14.5px;line-height:23px;color:#444}
.gifts .photo{position:absolute;left:613px;top:713px;width:512px;height:327px;background:linear-gradient(135deg,#6b7a86,#c9c2b4 45%,#3a3630)}
/* services */
.services{position:absolute;top:1100px;left:0;width:1200px;height:400px;background:var(--grey-bg)}
.svc{position:absolute;width:270px;height:178px;display:flex;flex-direction:column;align-items:center;justify-content:center;gap:18px;color:var(--purple);font-weight:700;font-size:18px}
.svc .circle{width:70px;height:70px;border-radius:50%;border:3px solid var(--orange);background:#fff;display:flex;align-items:center;justify-content:center}
.vline{position:absolute;width:1px;background:var(--line)}
.hline{position:absolute;height:1px;background:var(--line)}
/* vision */
.vision{position:absolute;top:1535px;left:0;width:1200px;height:375px;background:linear-gradient(110deg,#9b1f3a 0%,#5a2a78 35%,#2a3f8a 60%,#1a6a8a 100%);color:#fff;text-align:center}
.vision h2{position:absolute;top:58px;width:1200px;font-size:42px;font-weight:700}
.vision h3{position:absolute;top:112px;width:1200px;font-size:21px;font-weight:700}
.vision p{position:absolute;top:160px;width:1200px;font-size:14.5px;line-height:25px;padding:0 120px}
.btn-green{background:var(--green);font-size:16px;text-transform:uppercase}
/* speak */
.speak h2{position:absolute;top:1960px;width:1200px;text-align:center;color:var(--purple);font-size:36px;line-height:44px;font-weight:700}
/* prices */
.prices{position:absolute;top:2197px;left:0;width:1200px;height:308px;background:linear-gradient(90deg,#1a9cb5 0%,#5a8fa0 45%,#e8742a 100%);color:#fff;text-align:center}
.prices h2{position:absolute;top:50px;width:1200px;font-size:42px;font-weight:700}
.prices p{position:absolute;top:112px;width:1200px;font-size:20px;line-height:35px;font-weight:700}
.btn-red{background:var(--red)}
/* gallery */
.gallery .tile{position:absolute;width:343px}
/* contact */
.need{position:absolute;top:3127px;left:0;width:613px;height:423px;background:var(--teal);color:#fff}
.need h2{position:absolute;left:75px;top:40px;font-size:42px;font-weight:700}
.need .sub{position:absolute;left:75px;top:95px;font-size:17px;font-weight:700;line-height:25px}
.field{position:absolute;background:#fff;border-radius:2px;font-size:13px;color:#444;padding:10px 12px}
.need-photo{position:absolute;top:3127px;left:613px;width:587px;height:423px;background:linear-gradient(160deg,#5d6f8a,#8fa0b8 40%,#4f7a3a 80%,#9aa46a)}
/* footer */
.site-footer{position:absolute;top:3550px;left:0;width:1200px;height:410px;background:#fff}
.skyline{position:absolute;left:80px;top:60px;width:1040px;height:110px;background:linear-gradient(180deg,rgba(200,200,205,0) 0%,rgba(200,200,205,.35) 100%)}
.addr{position:absolute;left:90px;width:320px;font-size:13px;line-height:19px;color:#444}
.addr b{display:block;color:var(--purple);font-size:15px}
.pin{position:absolute;left:75px;width:12px;height:16px}
.footer-logo{left:460px;width:280px;top:210px;font-size:40px;line-height:1}
.footer-logo small{display:block;font-size:18px;letter-spacing:8px;margin-top:4px}
.social{position:absolute;left:0;top:3598px;width:32px}
.social span{display:block;width:32px;height:32px;margin-bottom:2px}
.bottom-bar{position:absolute;top:3960px;left:0;width:1200px;height:58px;background:var(--black);color:#ddd;font-size:11px;font-weight:700;text-transform:uppercase}
.bottom-bar .copy{position:absolute;left:90px;top:22px}
.bottom-bar nav{position:absolute;right:110px;top:22px;display:flex;gap:40px}
</style>
</head>
<body>

<header class="site-header">
  <div class="pill" style="left:140px;top:25px;height:26px"><span class="dot"></span>USA +1 (555) 010-4417</div>
  <div class="phones" style="left:75px;top:58px"><span><i class="flag flag-br"></i>+55 21 3000-0147</span><span><i class="flag flag-us"></i>+1 (555) 010-2290</span></div>
  <div class="contact-link" style="left:777px;top:30px"><span class="ico" style="background:var(--pink)"><svg width="18" height="18" viewBox="0 0 24 24" fill="#fff"><path d="M6.6 10.8a15 15 0 0 0 6.6 6.6l2.2-2.2c.3-.3.7-.4 1-.2 1.1.4 2.3.6 3.6.6.6 0 1 .4 1 1V20c0 .6-.4 1-1 1A17 17 0 0 1 3 4c0-.6.4-1 1-1h3.5c.6 0 1 .4 1 1 0 1.3.2 2.5.6 3.6.1.3 0 .7-.2 1z"/></svg></span>Talk to an<br>agent</div>
  <div class="contact-link" style="left:943px;top:30px"><span class="ico" style="background:var(--teal)"><svg width="18" height="18" viewBox="0 0 24 24" fill="none" stroke="#fff" stroke-width="2"><rect x="3" y="5" width="18" height="16" rx="2"/><path d="M3 10h18M8 3v4M16 3v4"/></svg></span>Schedule a<br>conversation</div>
</header>
<div class="logo-tab"><div class="brand">CORAL<small>PARLOR</small></div></div>

<section class="hero" role="img" aria-label="Photo of a Florida clubhouse with palm trees at sunset">
  <h1>Invest in Florida<br>and effectively tranquility</h1>
  <svg class="arrow" style="left:75px" viewBox="0 0 24 40"><path d="M20 4 6 20l14 16" fill="none" stroke="#fff" stroke-width="3"/></svg>
  <svg class="arrow" style="left:1101px" viewBox="0 0 24 40"><path d="M4 4l14 16L4 36" fill="none" stroke="#fff" stroke-width="3"/></svg>
  <div class="btn btn-orange" style="left:316px;top:356px;width:568px;height:54px;font-size:21px">Know The Best Investment Opportunities In Florida</div>
</section>

<section class="gifts">
  <h2>Gifts in Brazil and the United States</h2>
  <p style="top:755px">The Coral Parlor has a permanent Lounge in Rio de Janeiro, Brazil and Orlando, Florida. With an innovative concept of 360 ° assistance, advising clients who wish to buy a property in the United States, whether for Investing or Living.</p>
  <p style="top:868px">With the exclusive partnership of Halvorsen Homes, the largest construction company in the United States , we guarantee the best choices for you and your family! Our specialists have 360° vision to support you throughout the process and live the best experience in buying a property in America .</p>
  <div class="btn btn-orange" style="left:75px;top:996px;width:166px;height:44px">Read More</div>
  <div class="photo" role="img" aria-label="Photo of the lounge interior with sofas and a display wall"></div>
</section>

<section class="services">
  <div class="vline" style="left:330px;top:40px;height:360px"></div>
  <div class="vline" style="left:600px;top:40px;height:360px"></div>
  <div class="vline" style="left:870px;top:40px;height:360px"></div>
  <div class="hline" style="left:59px;top:219px;width:1082px"></div>

  <div class="svc" style="left:59px;top:44px"><span class="circle"><svg width="30" height="30" viewBox="0 0 24 24" fill="none" stroke="var(--purple)" stroke-width="2.2"><path d="M16 7c-1-1-2.4-1.5-4-1.5-2 0-3.5 1-3.5 2.7 0 4 7.5 2 7.5 6 0 1.8-1.6 3-4 3-1.7 0-3.2-.6-4.2-1.7M12 3v18"/></svg></span>Financing</div>
  <div class="svc" style="left:330px;top:44px"><span class="circle"><svg width="30" height="30" viewBox="0 0 24 24" fill="none" stroke="var(--purple)" stroke-width="2"><rect x="4" y="6" width="16" height="14" rx="1"/><path d="M4 9l8 5 8-5M9 3h6"/></svg></span>Financial Remittances</div>
  <div class="svc" style="left:600px;top:44px"><span class="circle"><svg width="30" height="30" viewBox="0 0 24 24" fill="none" stroke="var(--purple)" stroke-width="2"><path d="M2 12s4-7 10-7 10 7 10 7-4 7-10 7S2 12 2 12z"/><circle cx="12" cy="12" r="3" fill="var(--purple)"/></svg></span>Seen</div>
  <div class="svc" style="left:870px;top:44px"><span class="circle"><svg width="30" height="30" viewBox="0 0 24 24" fill="none" stroke="var(--purple)" stroke-width="2"><rect x="3" y="6" width="18" height="13" rx="1"/><circle cx="8.5" cy="12" r="2"/><path d="M13 10h5M13 14h5M10 4h4"/></svg></span>Eb-5 (Green Card)</div>

  <div class="svc" style="left:59px;top:222px"><span class="circle"><svg width="30" height="30" viewBox="0 0 24 24" fill="none" stroke="var(--purple)" stroke-width="2"><rect x="5" y="3" width="14" height="18" rx="1"/><path d="M8 7h8M8 11h2M12 11h2M16 11h0M8 15h2M12 15h2M8 18h2M12 18h2"/></svg></span>Accounting</div>
  <div class="svc" style="left:330px;top:222px"><span class="circle"><svg width="30" height="30" viewBox="0 0 24 24" fill="none" stroke="var(--purple)" stroke-width="2"><path d="M6 3h9l4 4v14H6z"/><path d="M9 11h7M9 14h7M9 17h5"/></svg></span>Documentation</div>
  <div class="svc" style="left:600px;top:222px"><span class="circle"><svg width="30" height="30" viewBox="0 0 24 24" fill="var(--purple)"><path d="M7 6a5 5 0 0 1 10 0v5H7z"/><rect x="3" y="10" width="4" height="7" rx="2"/><rect x="17" y="10" width="4" height="7" rx="2"/><rect x="6" y="13" width="12" height="4"/><path d="M6 17h2v3H6zM16 17h2v3h-2z"/></svg></span>Furniture</div>
  <div class="svc" style="left:870px;top:222px"><span class="circle"><svg width="30" height="30" viewBox="0 0 24 24" fill="var(--purple)"><path d="M12 3 2 12h3v9h5v-6h4v6h5v-9h3z"/></svg></span>Home Administration</div>
</section>

<section class="vision" role="img" aria-label="Aerial photo of a Florida residential development in a colour overlay">
  <h2>360º VISION</h2>
  <h3>We take care of absolutely everything to make you feel at home in Florida!</h3>
  <p>360° service from Brazilian to Brazilian.<br>Our specialists will assist you in everything you need to achieve your dream of investing or living in America, with comfort and above all safety . From the choice of the best property to the opening of companies and financial remittances.</p>
  <div class="btn btn-green" style="left:407px;top:260px;width:386px;height:51px">Do you want to talk via ChatWave?</div>
</section>

<section class="speak">
  <h2>Do You Want To Speak<br>With A Specialist?</h2>
  <div class="btn btn-orange" style="left:474px;top:2090px;width:252px;height:45px">Agendar Atendimento</div>
</section>

<section class="prices">
  <h2>Receives Prices And Plants Of Buildings</h2>
  <p>Have at your disposal information about our properties.<br>You will have an always up-to-date list of our available launches and homes.</p>
  <div class="btn btn-red" style="left:474px;top:198px;width:252px;height:48px">Request Here</div>
</section>

<section class="gallery">
  <div class="tile" style="left:75px;top:2558px;height:207px;background:linear-gradient(135deg,#3a3530,#b8ad9a 55%,#e6e1d8)" role="img" aria-label="Photo of a modern kitchen interior"></div>
  <div class="tile" style="left:429px;top:2558px;height:207px;background:linear-gradient(135deg,#8a8276,#ddd6c8 55%,#a59a88)" role="img" aria-label="Photo of a bright living room"></div>
  <div class="tile" style="left:782px;top:2558px;height:207px;background:linear-gradient(135deg,#2a2018,#8a6a48 50%,#3a2e22)" role="img" aria-label="Photo of a clubhouse bar lounge"></div>
  <div class="tile" style="left:75px;top:2775px;height:210px;background:linear-gradient(180deg,#3f86c8,#8fbfe0 55%,#3b6a2a)" role="img" aria-label="Photo of a resort entrance sign with palm trees"></div>
  <div class="tile" style="left:429px;top:2775px;height:210px;background:linear-gradient(180deg,#1a2a45,#6a5a48 55%,#2a2a2a)" role="img" aria-label="Photo of a lit fountain at dusk"></div>
  <div class="tile" style="left:782px;top:2775px;height:210px;background:linear-gradient(180deg,#7ab0e0,#c8c8c4 55%,#5a8a3a)" role="img" aria-label="Photo of a two-storey family home"></div>
  <div class="btn btn-orange" style="left:530px;top:3027px;width:140px;height:43px">View All</div>
</section>

<section class="need">
  <h2>What You Need</h2>
  <div class="sub">We Are Here To Help You<br>Do not hesitate to speak with one of our experts</div>
  <div class="field" style="left:75px;top:163px;width:247px;height:43px">Name</div>
  <div class="field" style="left:340px;top:163px;width:247px;height:43px">Email Address</div>
  <div class="field" style="left:75px;top:216px;width:512px;height:86px">Message</div>
  <div class="btn btn-orange" style="left:75px;top:321px;width:139px;height:43px">Submit</div>
</section>
<div class="need-photo" role="img" aria-label="Photo of a family in front of their new house"></div>

<footer class="site-footer">
  <div class="skyline" role="img" aria-label="Faint city skyline illustration"></div>
  <svg class="pin" style="top:175px" viewBox="0 0 12 16"><path d="M6 0a6 6 0 0 0-6 6c0 4.5 6 10 6 10s6-5.5 6-10a6 6 0 0 0-6-6z" fill="var(--pink)"/><circle cx="6" cy="6" r="2" fill="#fff"/></svg>
  <div class="addr" style="top:174px"><b>Mar Azul Center</b>1st Floor beside the Café Court Av. Atlântica 4410, Recreio - RJ - Brazil</div>
  <svg class="pin" style="top:257px" viewBox="0 0 12 16"><path d="M6 0a6 6 0 0 0-6 6c0 4.5 6 10 6 10s6-5.5 6-10a6 6 0 0 0-6-6z" fill="var(--pink)"/><circle cx="6" cy="6" r="2" fill="#fff"/></svg>
  <div class="addr" style="top:256px"><b>Orlando</b>2140 Palm Court Avenue, Suite 118, Orlando, USA</div>
  <svg class="pin" style="top:334px" viewBox="0 0 12 16"><rect y="3" width="12" height="10" rx="2" fill="var(--pink)"/><path d="M1 4l5 4 5-4" stroke="#fff" fill="none"/></svg>
  <div class="addr" style="top:332px;color:var(--purple);font-weight:700">contact@thecoralparlor.com</div>

  <div class="brand footer-logo">CORAL<small>PARLOR</small></div>

  <div class="pill" style="left:830px;top:174px;height:35px;font-size:17px"><span class="dot"></span>USA +1 (555) 010-4417</div>
  <div class="phones" style="left:793px;top:219px"><span><i class="flag flag-br"></i>+55 21 3000-0147</span><span><i class="flag flag-us"></i>+1 (555) 010-2290</span></div>
  <div class="contact-link" style="left:785px;top:268px"><span class="ico" style="background:var(--pink)"><svg width="18" height="18" viewBox="0 0 24 24" fill="#fff"><path d="M6.6 10.8a15 15 0 0 0 6.6 6.6l2.2-2.2c.3-.3.7-.4 1-.2 1.1.4 2.3.6 3.6.6.6 0 1 .4 1 1V20c0 .6-.4 1-1 1A17 17 0 0 1 3 4c0-.6.4-1 1-1h3.5c.6 0 1 .4 1 1 0 1.3.2 2.5.6 3.6.1.3 0 .7-.2 1z"/></svg></span>Talk to an<br>agent</div>
  <div class="contact-link" style="left:950px;top:268px"><span class="ico" style="background:var(--teal)"><svg width="18" height="18" viewBox="0 0 24 24" fill="none" stroke="#fff" stroke-width="2"><rect x="3" y="5" width="18" height="16" rx="2"/><path d="M3 10h18M8 3v4M16 3v4"/></svg></span>Schedule a<br>conversation</div>
</footer>

<div class="social" aria-label="Share links">
  <span style="background:#1da1f2"></span>
  <span style="background:#3b5998"></span>
  <span style="background:#dd4b39"></span>
  <span style="background:#cb2027"></span>
  <span style="background:#7d7d7d"></span>
  <span style="background:var(--green)"></span>
</div>

<div class="bottom-bar">
  <div class="copy">© 2017 - The Coral Parlor by Northwave</div>
  <nav><span>Home</span><span>Properties</span><span>Magazine</span><span>Contact</span><span>Terms of use</span></nav>
</div>

</body>
</html>
```